Business Card Design for Mortgage Broking Business

We need to redesign the business card. Mortgage broking business, doing home loan and commercial loans, existing logo, also QLBT member logo. design style needs to be simple, professional, elegant.

once final, need to setup for a team of different names and contact details.

Industry/Entity Type

Loan

Contact Information for Business Card

Name; Mobile; Email; Address; Tel; Fax; Australian Credit Licence: 618204

```html
<!DOCTYPE html>
<html lang="en">
<head>
<meta charset="UTF-8">
<title>QLBT – Business Card</title>
<link href="https://fonts.googleapis.com/css2?family=Exo+2:wght@400;500;600;700&display=swap" rel="stylesheet">
<style>
  :root {
    --navy: #2e4b78;
    --brand-blue: #1f4f8f;
    --green: #4bb74a;
    --ink: #2b2b2b;
    --paper: #ffffff;
    --backdrop: #e9e9eb;
    --on-navy: #ffffff;
  }
  * { box-sizing: border-box; margin: 0; padding: 0; }
  html, body { width: 1200px; height: 900px; overflow: hidden; }
  body {
    background: var(--backdrop);
    font-family: "Exo 2", sans-serif;
    position: relative;
  }
  .card {
    position: absolute;
    left: 280px;
    width: 640px;
    height: 390px;
    background: var(--paper);
    overflow: hidden;
    box-shadow: 0 4px 14px rgba(0,0,0,0.12);
  }
  .card--back { top: 30px; }
  .card--front { top: 470px; }

  .brand {
    position: absolute;
    display: flex;
    align-items: center;
    gap: 14px;
  }
  .brand__square {
    width: 32px;
    height: 32px;
    background: var(--green);
    flex: none;
  }
  .brand__name {
    font-weight: 700;
    color: var(--brand-blue);
    letter-spacing: 1px;
    line-height: 1;
  }
  .card--back .brand {
    left: 50%; top: 50%;
    transform: translate(-50%, -50%);
  }
  .card--back .brand__square { width: 44px; height: 44px; }
  .card--back .brand__name { font-size: 48px; }
  .card--front .brand { left: 48px; top: 112px; }
  .card--front .brand__name { font-size: 30px; }

  .front__wave { position: absolute; inset: 0; }

  .person {
    position: absolute;
    left: 262px;
    top: 42px;
  }
  .person__name {
    font-size: 22px;
    font-weight: 500;
    color: var(--green);
    letter-spacing: 2px;
    text-transform: uppercase;
  }
  .person__role {
    font-size: 14px;
    color: var(--ink);
    margin-top: 4px;
  }

  .contacts {
    position: absolute;
    right: 84px;
    top: 214px;
    list-style: none;
    color: var(--on-navy);
    font-size: 12.5px;
    letter-spacing: 0.6px;
  }
  .contacts li {
    display: flex;
    align-items: center;
    gap: 14px;
    height: 24px;
    justify-content: flex-end;
  }
  .contacts svg { width: 14px; height: 14px; flex: none; }

  .footer {
    position: absolute;
    left: 30px;
    right: 30px;
    bottom: 20px;
    display: flex;
    justify-content: space-between;
    color: var(--on-navy);
    font-size: 12.5px;
    letter-spacing: 0.6px;
  }
</style>
</head>
<body>

  <section class="card card--back" aria-label="Card back">
    <div class="brand">
      <span class="brand__square"></span>
      <span class="brand__name">QLBT</span>
    </div>
  </section>

  <section class="card card--front" aria-label="Card front">
    <svg class="front__wave" viewBox="0 0 640 390" preserveAspectRatio="none" aria-hidden="true">
      <path d="M0 262 C 120 262, 220 250, 300 228 C 390 202, 400 172, 460 170 C 540 168, 600 168, 640 168 L640 390 L0 390 Z" fill="var(--navy)"/>
      <path d="M250 238 C 320 222, 360 200, 395 184" stroke="var(--green)" stroke-width="6" fill="none"/>
      <path d="M405 179 C 425 172, 440 168, 470 167" stroke="var(--green)" stroke-width="6" fill="none"/>
      <path d="M482 166 L 640 166" stroke="var(--green)" stroke-width="6" fill="none"/>
    </svg>

    <div class="brand">
      <span class="brand__square"></span>
      <span class="brand__name">QLBT</span>
    </div>

    <div class="person">
      <p class="person__name">Daniel Whitford</p>
      <p class="person__role">Managing Director</p>
    </div>

    <ul class="contacts">
      <li>07 3184 5520
        <svg viewBox="0 0 16 16" fill="none" stroke="#fff" stroke-width="1.5"><path d="M4 2l2.5 3-1.5 1.5c.8 1.8 2.4 3.4 4.5 4.5L11 9.5l3 2.5-1.5 2C7 14 2 9 2 3.5z"/></svg>
      </li>
      <li>07 3184 5520
        <svg viewBox="0 0 16 16" fill="none" stroke="#fff" stroke-width="1.5"><rect x="4.5" y="1.5" width="7" height="13" rx="1"/><line x1="7" y1="12" x2="9" y2="12"/></svg>
      </li>
      <li>07 3184 5520
        <svg viewBox="0 0 16 16" fill="none" stroke="#fff" stroke-width="1.5"><rect x="2" y="6" width="12" height="7"/><rect x="4.5" y="2" width="7" height="4"/></svg>
      </li>
      <li>d.whitford@harbourlend.com.au
        <svg viewBox="0 0 16 16" fill="none" stroke="#fff" stroke-width="1.5"><rect x="1.5" y="3.5" width="13" height="9"/><path d="M1.5 3.5L8 9l6.5-5.5"/></svg>
      </li>
      <li>www.harbourlend.com.au
        <svg viewBox="0 0 16 16" fill="none" stroke="#fff" stroke-width="1.3"><circle cx="8" cy="8" r="6.5"/><ellipse cx="8" cy="8" rx="2.8" ry="6.5"/><line x1="1.5" y1="8" x2="14.5" y2="8"/></svg>
      </li>
    </ul>

    <div class="footer">
      <p class="footer__address">Level 18, 42 Kendall Street, Brisbane QLD</p>
      <p class="footer__licence">Australian Credit Licence 618204</p>
    </div>
  </section>

</body>
</html>
```